Frostvale Harborline LLC

we need a business card design

Industry/Entity Type

hvac

Contact Information for Business Card

my logo

Requirements
Must have
• my logo and same colors

```html
<!DOCTYPE html>
<html lang="en">
<head>
<meta charset="utf-8">
<title>Frostvale Harborline LLC – Business Card</title>
<link rel="stylesheet" href="https://fonts.googleapis.com/css2?family=Montserrat:wght@400;500;700;800&display=swap">
<style>
  :root {
    --brand-blue: #0560a8;
    --deep-blue: #0b57a0;
    --sun-yellow: #f8b84e;
    --ink: #1d1d1f;
    --paper: #ffffff;
    --backdrop: #eceaee;
  }
  * { box-sizing: border-box; margin: 0; padding: 0; }
  html, body { width: 1200px; height: 1108px; overflow: hidden; }
  body {
    background: var(--backdrop);
    font-family: "Montserrat", Arial, sans-serif;
    color: var(--ink);
    position: relative;
  }
  .card { position: absolute; overflow: hidden; }
  .card-front { left: 219px; top: 50px; width: 775px; height: 473px; background: var(--paper); }
  .card-back { left: 217px; top: 568px; width: 777px; height: 456px; background: var(--brand-blue); }

  .front-waves { position: absolute; inset: 0; width: 100%; height: 100%; }

  .brand-mark {
    position: absolute; left: 100px; top: 178px; width: 280px;
    display: flex; align-items: center; gap: 14px;
  }
  .brand-dot { width: 34px; height: 34px; border-radius: 50%; background: var(--sun-yellow); flex: none; }
  .brand-name {
    font-weight: 800; font-size: 26px; line-height: 1.15; color: var(--brand-blue);
  }

  .divider {
    position: absolute; left: 395px; top: 127px; width: 3px; height: 205px; background: var(--brand-blue);
  }
  .contact { position: absolute; left: 412px; top: 124px; }
  .person-name { font-weight: 700; font-size: 30px; color: var(--deep-blue); line-height: 1.1; }
  .person-role { font-size: 18px; margin-top: 4px; }
  .address { font-size: 18px; line-height: 1.25; margin-top: 14px; }
  .contact-list { list-style: none; margin-top: 12px; }
  .contact-list li { display: flex; align-items: center; gap: 10px; font-size: 18px; line-height: 28px; }
  .contact-list svg { width: 18px; height: 18px; flex: none; }

  .back-brand {
    position: absolute; inset: 0; display: flex; align-items: center; justify-content: center; gap: 22px;
  }
  .back-brand .brand-dot { width: 60px; height: 60px; }
  .back-brand .brand-name { color: var(--paper); font-size: 48px; text-align: left; }
</style>
</head>
<body>
  <section class="card card-front">
    <svg class="front-waves" viewBox="0 0 787 480" preserveAspectRatio="none" aria-hidden="true">
      <path fill="var(--sun-yellow)" d="M160,362 C300,368 420,418 560,440 C660,452 730,410 787,330 L787,385 C700,455 600,468 500,452 C380,432 280,382 160,362 Z"/>
      <path fill="var(--brand-blue)" d="M0,390 C120,358 250,378 420,430 C560,470 690,470 787,402 L787,480 L0,480 Z"/>
    </svg>

    <div class="brand-mark">
      <span class="brand-dot"></span>
      <span class="brand-name">Frostvale Harborline LLC</span>
    </div>

    <div class="divider"></div>

    <div class="contact">
      <h1 class="person-name">Dana Whitfield</h1>
      <p class="person-role">Managing Director</p>
      <p class="address">48 Orchard Lane,<br>Milbrook, NY 12545</p>
      <ul class="contact-list">
        <li>
          <svg viewBox="0 0 18 18"><rect x="4" y="1" width="10" height="16" rx="2" fill="none" stroke="var(--sun-yellow)" stroke-width="2"/><circle cx="9" cy="14" r="1" fill="var(--sun-yellow)"/></svg>
          +1 (555) 014-2298
        </li>
        <li>
          <svg viewBox="0 0 18 18"><rect x="1" y="4" width="16" height="11" fill="var(--sun-yellow)"/><path d="M1,4 L9,10 L17,4" fill="none" stroke="#fff" stroke-width="1.5"/></svg>
          hello@frostvalellc.com
        </li>
        <li>
          <svg viewBox="0 0 18 18"><circle cx="9" cy="9" r="7.5" fill="var(--sun-yellow)"/><path d="M1.5,9 H16.5 M9,1.5 C5,5 5,13 9,16.5 M9,1.5 C13,5 13,13 9,16.5" fill="none" stroke="#fff" stroke-width="1.2"/></svg>
          www.frostvalellc.com
        </li>
      </ul>
    </div>
  </section>

  <section class="card card-back">
    <div class="back-brand">
      <span class="brand-dot"></span>
      <span class="brand-name">Frostvale<br>Harborline LLC</span>
    </div>
  </section>
</body>
</html>
```